Kestrova - presentation for a remote DBA team offering data platform management

We need a website design for wordpress site called Kestrova.cz
We deliver remote database and data platform administration and development, oversee the database administrators, consult and train the personnel responsible for the database operations. The website should include several sections, home page with graphics elements supporting the name and service - remote dba work; blog section; service introduction and description, team introduction and description, download section for documents, presentations etc.

Target Market(s)

small and medium business companies requiring remote DBA service

Number of Pages Required

3 page

Font styles to use
Sans Serif

Colors

Designer to choose colors to be used in the design.

Requirements
Must have
• The website should have several sections to introduce the services, blog, team introduction, downloads

```html
<!DOCTYPE html>
<html lang="en">
<head>
<meta charset="utf-8">
<title>Kestrova – Remote DBA Team</title>
<link href="https://fonts.googleapis.com/css2?family=Poppins:ital,wght@0,400;0,500;0,600;0,700;1,400&family=Roboto:wght@400;500;700;900&display=swap" rel="stylesheet">
<style>
:root{
  --navy:#0f1a2b;
  --blue:#1f6fc1;
  --blue-deep:#0b4a9b;
  --teal:#23a6a3;
  --ink:#1b1f27;
  --text:#444a55;
  --muted:#7a808a;
  --light:#f1f2f4;
  --white:#ffffff;
}
*{box-sizing:border-box;margin:0;padding:0}
html,body{width:1200px;height:4119px;overflow:hidden}
body{font-family:"Poppins",sans-serif;color:var(--text);background:var(--white);position:relative}
.abs{position:absolute}
h1,h2,h3,h4{font-family:"Roboto",sans-serif;color:var(--ink)}
.btn{display:inline-block;border-radius:20px;color:var(--white);font:600 13px "Poppins",sans-serif;text-transform:uppercase;padding:0 24px;line-height:36px;background:linear-gradient(90deg,var(--teal),var(--blue))}
.btn-outline{border:2px solid var(--ink);color:var(--ink);background:none;line-height:24px;font-size:11px;padding:0 16px}
p.body{font-size:13.5px;line-height:29px}

/* hero */
.hero{left:0;top:0;width:1200px;height:673px;background:linear-gradient(110deg,#2b3340 0%,#121924 45%,#1d2633 100%)}
.hero-photo{left:560px;top:0;width:640px;height:640px;background:radial-gradient(circle at 60% 40%,#4a5868 0%,#1b2330 70%)}
.logo{left:135px;top:40px;display:flex;align-items:center;gap:12px;color:var(--white);font:700 34px "Roboto",sans-serif}
.logo i{width:40px;height:40px;border-radius:50%;background:var(--teal)}
.nav{left:370px;top:62px;display:flex;gap:24px;font:500 14px "Poppins",sans-serif;color:var(--white)}
.signin{left:955px;top:52px;width:113px;height:36px;border:2px solid var(--white);border-radius:18px;color:var(--white);font:600 13px "Poppins",sans-serif;display:flex;align-items:center;justify-content:center;gap:6px}
.hero h1{left:130px;top:232px;color:var(--white);font-size:40px;line-height:48px;font-weight:700}
.hero-text{left:130px;top:342px;width:360px;color:#e4e7eb;font-size:13.5px;line-height:24px}
.dots{left:132px;top:492px;display:flex;gap:8px}
.dots span{width:9px;height:9px;border-radius:50%;background:var(--white)}
.dots span:first-child{box-shadow:0 0 0 3px #121924,0 0 0 4px var(--white)}

/* welcome */
.monitor{left:133px;top:795px;width:390px;height:250px;border:10px solid #1b1f27;border-radius:6px;background:linear-gradient(135deg,#27384c,#5a6b7e)}
.monitor-base{left:133px;top:1045px;width:390px;height:30px;background:linear-gradient(#e4e6ea,#b9bcc2);border-radius:0 0 6px 6px}
.welcome h2{left:573px;top:805px;font-size:34px;font-weight:500}
.welcome h2 b,.accent{color:var(--blue)}
.welcome p{left:573px;top:865px;width:495px}

/* remote */
.remote{left:0;top:1208px;width:1200px;height:486px;background:var(--light)}
.remote-photo{left:570px;top:0;width:630px;height:486px;background:linear-gradient(90deg,var(--light) 0%,#b8bdc4 25%,#6e747c 70%,#8a8f96 100%)}
.remote h2{left:130px;top:105px;font-size:29px;line-height:42px;font-weight:700}
.remote p{left:130px;top:202px;width:475px}

/* services */
.services{left:0;top:1694px;width:1200px;height:758px;background:linear-gradient(135deg,#1c64b5,#0d4a9a 60%,#1e6ac0)}
.services h2{left:0;top:52px;width:1200px;text-align:center;color:var(--white);font-size:38px;font-weight:400}
.card{width:294px;height:245px;background:var(--white);text-align:center;padding:28px 18px 0}
.card svg{width:74px;height:74px}
.card h3{font:500 14px "Poppins",sans-serif;color:var(--ink);text-transform:uppercase;margin:14px 0 12px}
.card p{font-size:11.5px;line-height:22px}

/* news */
.news-title{left:0;top:2525px;width:1200px;text-align:center;font-size:38px;font-weight:400}
.news-card{left:133px;top:2630px;width:933px;height:355px;background:var(--white);box-shadow:0 4px 18px rgba(0,0,0,.14)}
.news-card h3{left:48px;top:30px;width:380px;font-size:24px;line-height:38px;font-weight:700}
.meta{left:48px;top:118px;font:italic 12px "Poppins",sans-serif;color:var(--blue);display:flex;gap:26px}
.news-card p{left:48px;top:150px;width:420px;font-size:12.5px;line-height:28px}
.news-photo{left:490px;top:10px;width:434px;height:335px;background:linear-gradient(135deg,#0f2544,#2a5b8c 60%,#0b1a30)}
.arrow{width:24px;height:50px}

/* testimonial */
.testi{left:0;top:3111px;width:1200px;height:404px;background:linear-gradient(90deg,#1a9a9c,#1a6cbd)}
.quote-box{left:295px;top:37px;width:615px;height:227px;background:var(--white);border-radius:10px;padding:30px 50px 0 60px}
.quote-box p{font:italic 12.5px/24px "Poppins",sans-serif;color:var(--text)}
.qmark{font:700 40px "Roboto",sans-serif;color:var(--ink)}
.avatar{left:553px;top:238px;width:94px;height:94px;border-radius:50%;background:var(--teal);border:5px solid var(--white)}
.who{top:288px;color:var(--ink);font-size:13px}

/* clients */
.clients{left:0;top:3515px;width:1200px;height:165px;display:flex;justify-content:center;align-items:center;gap:74px;font:700 24px "Roboto",sans-serif;color:#9a9ea5}

/* footer */
.footer{left:0;top:3680px;width:1200px;height:351px;background:var(--light)}
.footer h4{font-size:18px;font-weight:600;text-transform:uppercase;color:var(--ink)}
.footer h4 span{color:var(--blue)}
.fcol{top:100px}
.contact-row{display:flex;gap:14px;font-size:12px;line-height:18px;margin-top:16px;color:var(--ink)}
.contact-row svg{flex:none;width:14px;height:14px;margin-top:2px}
.email{width:275px;height:38px;background:var(--white);border:1px solid #d4d6da;margin-top:16px;font-size:11px;color:var(--muted);padding:10px 14px}
.signup{display:inline-block;margin-top:16px;width:113px;line-height:38px;text-align:center;background:#55595f;color:var(--white);font:600 13px "Poppins",sans-serif}
.links{list-style:none;margin-top:12px;font-size:12px;line-height:23px;color:var(--ink)}
.links li::before{content:"▸ ";font-size:9px}
.social{display:flex;gap:7px;margin-top:20px}
.social span{width:28px;height:28px;border-radius:50%}
.bottom{left:0;top:4031px;width:1200px;height:88px;text-align:center;line-height:88px;font-size:12px;color:var(--ink)}
</style>
</head>
<body>

<header class="abs hero">
  <div class="abs hero-photo" role="img" aria-label="Businessman holding a tablet with a glowing cloud and network icons above it"></div>
  <div class="abs logo"><i></i>Kestrova</div>
  <nav class="abs nav"><span>HOME</span><span>ABOUT US</span><span>OUR SERVICES</span><span>BLOG</span><span>CLIENTS</span><span>CONTACT</span></nav>
  <div class="abs signin"><svg width="11" height="11" viewBox="0 0 10 10"><circle cx="5" cy="3" r="2.4" fill="#fff"/><path d="M0.5 10a4.5 4 0 0 1 9 0z" fill="#fff"/></svg>SIGN IN</div>
  <h1 class="abs">DATA PLATFORM<br>MANAGEMENT</h1>
  <p class="abs hero-text">Duis aute irure dolor in reprehenderit in voluptate velit esse cillum dolore eu fugiat nulla pariatur.</p>
  <a class="abs btn" style="left:130px;top:418px">Read more</a>
  <div class="abs dots"><span></span><span></span><span></span><span></span></div>
  <svg class="abs" style="left:0;top:620px" width="1200" height="54" viewBox="0 0 1200 54" preserveAspectRatio="none"><path d="M0 30 L40 22 L80 34 L130 20 L180 36 L230 24 L290 38 L340 26 L400 40 L460 28 L520 42 L580 30 L640 40 L700 26 L760 38 L820 24 L880 36 L940 22 L1000 34 L1060 20 L1120 32 L1200 18 L1200 54 L0 54Z" fill="#fff"/></svg>
</header>

<section class="welcome">
  <div class="abs monitor" role="img" aria-label="Monitor showing a cloud data management graphic"></div>
  <div class="abs monitor-base"></div>
  <h2 class="abs">WELCOME TO <b>KESTROVA</b></h2>
  <p class="abs body">Sed ut perspiciatis unde omnis iste natus error sit voluptatem accusantium doloremque laudantium, totam rem aperiam, eaque ipsa quae ab illo inventore veritatis et quasi architecto beatae vitae dicta sunt explicabo. Nemo enim ipsam voluptatem quia voluptas sit aspernatur aut odit aut fugit, sed quia consequuntur.</p>
  <a class="abs btn" style="left:573px;top:1040px;line-height:32px;font-size:12px">Read more</a>
</section>

<section class="abs remote">
  <div class="abs remote-photo" role="img" aria-label="Smiling team member in an office with colleagues working at a table"></div>
  <h2 class="abs">REMOTE DBA TEAM OFFERING<br>DATA PLATFORM MANAGEMENT</h2>
  <p class="abs body">Sed ut perspiciatis unde omnis iste natus error sit voluptatem accusantium doloremque laudantium, totam rem aperiam, eaque ipsa quae ab illo inventore veritatis et quasi architecto beatae vitae dicta sunt explicabo. Nemo enim ipsam voluptatem quia voluptas sit aspernatur</p>
  <a class="abs btn" style="left:130px;top:350px;line-height:32px;font-size:12px">Find out more</a>
</section>

<section class="abs services">
  <h2 class="abs"><b style="font-weight:700">OUR</b> SERVICES</h2>
  <div class="abs card" style="left:133px;top:158px">
    <svg viewBox="0 0 74 74" fill="none" stroke="#1f6fc1" stroke-width="2"><rect x="22" y="6" width="36" height="12"/><rect x="22" y="22" width="36" height="12"/><rect x="22" y="38" width="36" height="12"/><rect x="8" y="30" width="24" height="18" stroke="#23a6a3"/><path d="M14 60h46M37 50v10"/></svg>
    <h3>Data Platform Administration</h3>
    <p>Sed ut perspiciatis unde omnis iste natus error sit voluptatem accusantium doloremque laudantium, totam rem aperiam</p>
  </div>
  <div class="abs card" style="left:453px;top:158px">
    <svg viewBox="0 0 74 74" fill="none" stroke="#1f6fc1" stroke-width="2"><rect x="14" y="10" width="46" height="14"/><rect x="14" y="28" width="46" height="14"/><circle cx="22" cy="17" r="2" stroke="#23a6a3"/><circle cx="22" cy="35" r="2" stroke="#23a6a3"/><path d="M37 42v14M20 58h34"/><circle cx="37" cy="60" r="3"/></svg>
    <h3>Database Administrators</h3>
    <p>Sed ut perspiciatis unde omnis iste natus error sit voluptatem accusantium doloremque laudantium, totam rem aperiam</p>
  </div>
  <div class="abs card" style="left:772px;top:158px">
    <svg viewBox="0 0 74 74" fill="none" stroke="#23a6a3" stroke-width="2"><rect x="29" y="29" width="16" height="16" stroke="#1f6fc1"/><path d="M37 29V14M37 45v15M29 37H14M45 37h15M31 31L20 20M43 31l11-11M31 43L20 54M43 43l11 11"/><circle cx="37" cy="11" r="3"/><circle cx="37" cy="63" r="3"/><circle cx="11" cy="37" r="3"/><circle cx="63" cy="37" r="3"/></svg>
    <h3>Remote Database</h3>
    <p>Sed ut perspiciatis unde omnis iste natus error sit voluptatem accusantium doloremque laudantium, totam rem aperiam</p>
  </div>
  <div class="abs card" style="left:133px;top:426px">
    <svg viewBox="0 0 74 74" fill="none" stroke="#1f6fc1" stroke-width="2"><rect x="10" y="12" width="40" height="12"/><rect x="10" y="28" width="40" height="12"/><rect x="10" y="44" width="40" height="12"/><path d="M52 36l12 5v9c0 7-6 11-12 13-6-2-12-6-12-13v-9z" stroke="#23a6a3"/></svg>
    <h3>Database Operations</h3>
    <p>Sed ut perspiciatis unde omnis iste natus error sit voluptatem accusantium doloremque laudantium, totam rem aperiam</p>
  </div>
  <div class="abs card" style="left:453px;top:426px">
    <svg viewBox="0 0 74 74" fill="none" stroke="#1f6fc1" stroke-width="2"><circle cx="37" cy="16" r="6" stroke="#23a6a3"/><circle cx="16" cy="52" r="6"/><circle cx="58" cy="52" r="6"/><path d="M37 22v12M16 46V38h42v8"/><path d="M6 68a10 8 0 0 1 20 0M48 68a10 8 0 0 1 20 0"/></svg>
    <h3>DBA Team</h3>
    <p>Sed ut perspiciatis unde omnis iste natus error sit voluptatem accusantium doloremque laudantium, totam rem aperiam</p>
  </div>
  <div class="abs card" style="left:772px;top:426px">
    <svg viewBox="0 0 74 74" fill="none" stroke="#1f6fc1" stroke-width="2"><circle cx="37" cy="37" r="28" stroke="#23a6a3"/><path d="M24 44a8 8 0 0 1 2-15 11 11 0 0 1 21-3 8 8 0 0 1 3 18z"/><path d="M30 50v6M37 50v8M44 50v6"/></svg>
    <h3>Data Platform Development</h3>
    <p>Sed ut perspiciatis unde omnis iste natus error sit voluptatem accusantium doloremque laudantium, totam rem aperiam</p>
  </div>
</section>

<section class="news">
  <h2 class="abs news-title"><b style="font-weight:700">LATEST</b> NEWS</h2>
  <svg class="abs arrow" style="left:82px;top:2760px" viewBox="0 0 24 50"><path d="M20 2L4 25l16 23" fill="none" stroke="#8a8f96" stroke-width="2"/></svg>
  <svg class="abs arrow" style="left:1094px;top:2760px" viewBox="0 0 24 50"><path d="M4 2l16 23L4 48" fill="none" stroke="#8a8f96" stroke-width="2"/></svg>
  <article class="abs news-card">
    <h3 class="abs">QUIS AUTEM VEL EUM IURE REPREHENDERIT QUI IN</h3>
    <div class="abs meta"><span>▦ March 25, 2018</span><span>◌ 2 comments</span></div>
    <p class="abs">Sed ut perspiciatis unde omnis iste natus error sit voluptatem accusantium doloremque laudantium, totam rem aperiam, eaque ipsa quae ab illo intore veritatis et quasi architecto beatae vitae dicta sunt explicabo.</p>
    <a class="abs btn btn-outline" style="left:48px;top:292px">Learn more</a>
    <div class="abs news-photo" role="img" aria-label="Two engineers looking at a laptop in a server room with cloud icons"></div>
  </article>
</section>

<section class="abs testi">
  <svg class="abs arrow" style="left:230px;top:170px" viewBox="0 0 24 50"><path d="M20 2L4 25l16 23" fill="none" stroke="#fff" stroke-width="2"/></svg>
  <svg class="abs arrow" style="left:952px;top:170px" viewBox="0 0 24 50"><path d="M4 2l16 23L4 48" fill="none" stroke="#fff" stroke-width="2"/></svg>
  <div class="abs quote-box">
    <span class="abs qmark" style="left:22px;top:18px">“</span>
    <p>Nemo enim ipsam voluptatem quia voluptas sit aspernatur aut odit aut fugit, sed quia conseq magni dolores eos qui ratione voluptatem sequi nesciunt. Neque porro quisquam est, qui dolorem ipsum quia dolor sit amet, consectetur, adipisci velit, sed quia non numquam eius modi tempora incidunt ut labore et dolore magnam aliquam</p>
    <span class="abs qmark" style="left:418px;top:160px">”</span>
  </div>
  <div class="abs avatar" role="img" aria-label="Client portrait"></div>
  <span class="abs who" style="left:450px">Rowan Ellery</span>
  <span class="abs who" style="left:700px">Kestrova</span>
</section>

<section class="abs clients">
  <span>Strand</span><span>Velmora</span><span>Ostrum</span><span>Quillon</span><span>Fernly</span><span>Brightwell</span>
</section>

<footer class="abs footer">
  <svg class="abs" style="left:0;top:-14px" width="1200" height="30" viewBox="0 0 1200 30" preserveAspectRatio="none"><path d="M0 16L50 8 100 18 160 6 220 16 280 8 340 18 400 6 460 16 520 8 580 18 640 6 700 16 760 8 820 18 880 6 940 16 1000 8 1060 18 1120 8 1200 14V30H0Z" fill="#f1f2f4"/></svg>
  <div class="abs fcol" style="left:140px;width:220px">
    <h4>Contact <span>Us</span></h4>
    <div class="contact-row"><svg viewBox="0 0 14 14"><path d="M7 1a4 4 0 0 1 4 4c0 3-4 8-4 8S3 8 3 5a4 4 0 0 1 4-4z" fill="#1f6fc1"/></svg><span>Kestrova<br>Corran Lane VIC 3990</span></div>
    <div class="contact-row"><svg viewBox="0 0 14 14"><path d="M3 1l3 3-2 2a8 8 0 0 0 4 4l2-2 3 3-2 2C6 13 1 8 1 3z" fill="#1f6fc1"/></svg><span>Phone: +61 2 8000 4120</span></div>
    <div class="contact-row"><svg viewBox="0 0 14 14"><rect x="1" y="3" width="12" height="8" fill="#1f6fc1"/><path d="M1 3l6 5 6-5" stroke="#fff" fill="none"/></svg><span>Email: contact@kestrova.cz</span></div>
  </div>
  <div class="abs fcol" style="left:402px;width:290px">
    <h4>Sign up for <span>Newsletter</span></h4>
    <p style="font-size:11px;line-height:17px;margin-top:18px;color:var(--ink)">Excepteur sint occaecat cupidatat non proident, sunt in culpa qui officia deserunt</p>
    <div class="email">Enter email</div>
    <span class="signup">SIGN UP</span>
  </div>
  <div class="abs fcol" style="left:745px">
    <h4>Quick <span>Links</span></h4>
    <ul class="links"><li>Home</li><li>About Us</li><li>Our Services</li><li>Blog</li><li>Clients</li><li>Contact</li></ul>
  </div>
  <div class="abs fcol" style="left:928px">
    <h4>Follow <span>Us</span></h4>
    <div class="social"><span style="background:#3b5a9a"></span><span style="background:#8a3ab9"></span><span style="background:#d7262b"></span><span style="background:#1da1f2"></span></div>
  </div>
</footer>
<div class="abs bottom">Kestrova © 2018 All Rights Reserved | Privacy Policy | Terms and Conditions</div>

</body>
</html>
```